Veldmark Supplies Business Card

Professional business card that stand out to our potential customers. Front and back with clean modern design

Industry/Entity Type

Oil and gas

Contact Information for Business Card

Name, address, website , office phone and cell number

Requirements
Must have
• Editable files for each employee

```html
<!DOCTYPE html>
<html lang="en">
<head>
<meta charset="utf-8">
<title>Veldmark Supplies Business Card</title>
<link rel="stylesheet" href="https://fonts.googleapis.com/css2?family=Montserrat:wght@400;500;600;700&display=swap">
<style>
  :root {
    --backdrop: #1f1f21;
    --cyan: #0bb0d2;
    --red: #e82a2a;
    --ink: #1b1b1b;
    --white: #ffffff;
  }
  * { box-sizing: border-box; margin: 0; padding: 0; }
  html, body {
    width: 1200px; height: 874px; overflow: hidden;
    background: var(--backdrop);
    font-family: "Montserrat", sans-serif;
  }
  .card {
    position: absolute; left: 250px;
    width: 700px; height: 400px;
    border-radius: 22px; overflow: hidden;
  }
  .card--front { top: 27px; background: var(--cyan); }
  .card--back { top: 447px; background: var(--white); }

  .wordmark {
    display: flex; align-items: center; gap: 12px;
    font-weight: 700; text-transform: uppercase; letter-spacing: 1px;
  }
  .wordmark__square { width: 22px; height: 22px; }

  .card--front .wordmark {
    position: absolute; left: 0; right: 0; top: 170px;
    justify-content: center;
    font-size: 40px; color: var(--white);
  }
  .card--front .wordmark__square { width: 34px; height: 34px; background: var(--red); }

  .card--back .wordmark {
    position: absolute; left: 40px; top: 172px;
    font-size: 24px; color: var(--red);
    width: 270px; line-height: 1.15;
  }
  .card--back .wordmark__square { background: var(--red); flex: none; }

  .divider {
    position: absolute; left: 345px; top: 92px;
    width: 2px; height: 180px; background: var(--red);
  }
  .person { position: absolute; left: 372px; top: 92px; }
  .person__name { font-size: 28px; font-weight: 700; color: var(--red); }
  .person__title { font-size: 15px; color: var(--ink); margin-top: 2px; }

  .contacts { position: absolute; left: 372px; top: 170px; list-style: none; }
  .contacts li {
    display: flex; align-items: center; gap: 10px;
    font-size: 15px; color: var(--ink); height: 24px;
  }
  .contacts svg { width: 13px; height: 13px; fill: var(--cyan); flex: none; }

  .address-band {
    position: absolute; left: 0; right: 0; top: 282px; height: 82px;
    background: var(--cyan);
    display: flex; align-items: center; justify-content: center;
    color: var(--white); font-size: 16px; letter-spacing: 0.5px;
  }
</style>
</head>
<body>

<section class="card card--front">
  <div class="wordmark"><span class="wordmark__square"></span>Veldmark Supplies</div>
</section>

<section class="card card--back">
  <div class="wordmark"><span class="wordmark__square"></span>Veldmark Supplies</div>

  <div class="divider"></div>

  <div class="person">
    <div class="person__name">Tomas Reinholt</div>
    <div class="person__title">President</div>
  </div>

  <ul class="contacts">
    <li><svg viewBox="0 0 16 16"><path d="M2 6c0-2 3-4 6-4s6 2 6 4v1h-3V5.5C10 5 9 4.7 8 4.7S6 5 5 5.5V7H2zM4 8h8l1 6H3z"/></svg>+1.555.210.0400 x123</li>
    <li><svg viewBox="0 0 16 16"><path d="M3 1l3 1 1 3-2 1.5c1 2 2.5 3.5 4.5 4.5L11 9l3 1 1 3-2 2C7 14 2 9 1 3z"/></svg>+1.555.318.642</li>
    <li><svg viewBox="0 0 16 16"><path d="M1 3h14v2L8 9 1 5zM1 7l7 4 7-4v6H1z"/></svg>info@veldmarksupplies.com</li>
    <li><svg viewBox="0 0 16 16"><circle cx="8" cy="8" r="7"/></svg>www.veldmarksupplies.com</li>
  </ul>

  <div class="address-band">42 Ridgeline Avenue Marlow, TX 79701 USA</div>
</section>

</body>
</html>
```